Stationery and Business Card Design

We need stationary design for our new company lanternfold. Lanternfold is a company that provides city apartment rentals for tourists in Athens We need business cards, letterheads for A4 and A5 and envelopes for A4 A5. The design needs to be modern, friendly and corporate.

Target Market(s)

City Tourists

Industry/Entity Type

Tourism

```html
<!DOCTYPE html>
<html lang="en">
<head>
<meta charset="utf-8">
<title>Lanternfold Apartments – Stationery</title>
<link href="https://fonts.googleapis.com/css2?family=Montserrat:wght@400;500&display=swap" rel="stylesheet">
<style>
  :root {
    --brand-plum: #7b1f51;
    --brand-charcoal: #3a3a3c;
    --paper: #f4f4f4;
    --envelope: #f8f8f8;
    --watermark: #e8e8e8;
    --backdrop: #d7d6d9;
    --ink: #3c3c3c;
    --rule: #8a8a8a;
  }
  * { box-sizing: border-box; margin: 0; padding: 0; }
  html, body { width: 1200px; height: 991px; overflow: hidden; }
  body {
    background: var(--backdrop);
    font-family: "Montserrat", sans-serif;
    position: relative;
  }

  /* Envelopes */
  .envelope {
    position: absolute;
    background: var(--envelope);
  }
  .envelope--a4 { left: 154px; top: 106px; width: 484px; height: 684px; }
  .envelope--a5 { left: 773px; top: 330px; width: 334px; height: 476px; }
  .envelope__flap { position: absolute; left: 0; top: 0; width: 100%; display: block; }
  .envelope__seal {
    position: absolute; left: 50%; transform: translateX(-50%);
    background: #ffffff;
  }
  .envelope--a4 .envelope__seal { top: 21px; width: 32px; height: 32px; }
  .envelope--a5 .envelope__seal { top: 14px; width: 22px; height: 22px; }

  /* Letterheads */
  .letterhead {
    position: absolute;
    background: var(--paper);
    display: flex; flex-direction: column; align-items: center;
  }
  .letterhead--a4 { left: 92px; top: 201px; width: 483px; height: 683px; padding-top: 45px; }
  .letterhead--a5 { left: 717px; top: 402px; width: 341px; height: 482px; padding-top: 34px; }

  .brand-mark { background: var(--brand-plum); }
  .letterhead--a4 .brand-mark { width: 44px; height: 44px; }
  .letterhead--a5 .brand-mark { width: 31px; height: 31px; }

  .brand-name {
    color: var(--brand-plum);
    font-weight: 400;
    letter-spacing: -0.5px;
    line-height: 1;
  }
  .letterhead--a4 .brand-name { font-size: 26px; margin-top: 10px; }
  .letterhead--a5 .brand-name { font-size: 18px; margin-top: 8px; }

  .brand-tagline {
    display: flex; align-items: center;
    color: var(--brand-plum);
    text-transform: uppercase;
    font-weight: 500;
  }
  .brand-tagline::before, .brand-tagline::after {
    content: ""; display: block; height: 1px; background: var(--rule);
  }
  .letterhead--a4 .brand-tagline { font-size: 7.5px; letter-spacing: 2.6px; margin-top: 4px; gap: 6px; }
  .letterhead--a4 .brand-tagline::before, .letterhead--a4 .brand-tagline::after { width: 26px; }
  .letterhead--a5 .brand-tagline { font-size: 5.5px; letter-spacing: 1.8px; margin-top: 3px; gap: 4px; }
  .letterhead--a5 .brand-tagline::before, .letterhead--a5 .brand-tagline::after { width: 20px; }

  .letterhead__address {
    color: var(--ink);
    text-align: center;
    font-style: normal;
  }
  .letterhead--a4 .letterhead__address { font-size: 7px; line-height: 10px; margin-top: 14px; }
  .letterhead--a5 .letterhead__address { font-size: 5px; line-height: 7px; margin-top: 11px; }

  .letterhead__watermark {
    position: absolute; background: var(--watermark);
  }
  .letterhead--a4 .letterhead__watermark { left: 95px; top: 280px; width: 291px; height: 291px; }
  .letterhead--a5 .letterhead__watermark { left: 68px; top: 198px; width: 205px; height: 205px; }

  .letterhead__footer-bar {
    position: absolute; left: 0; bottom: 0; width: 100%; display: flex;
  }
  .footer-bar__left { background: var(--brand-charcoal); height: 100%; }
  .footer-bar__right { background: var(--brand-plum); height: 100%; flex: 1; }
  .letterhead--a4 .letterhead__footer-bar { height: 10px; }
  .letterhead--a4 .footer-bar__left { width: 240px; }
  .letterhead--a5 .letterhead__footer-bar { height: 7px; }
  .letterhead--a5 .footer-bar__left { width: 169px; }
</style>
</head>
<body>

  <div class="envelope envelope--a4">
    <svg class="envelope__flap" viewBox="0 0 484 70" height="70" aria-hidden="true">
      <polygon points="0,0 484,0 464,70 20,70" fill="var(--brand-plum)"/>
    </svg>
    <div class="envelope__seal"></div>
  </div>

  <div class="envelope envelope--a5">
    <svg class="envelope__flap" viewBox="0 0 334 48" height="48" aria-hidden="true">
      <polygon points="0,0 334,0 320,48 14,48" fill="var(--brand-plum)"/>
    </svg>
    <div class="envelope__seal"></div>
  </div>

  <section class="letterhead letterhead--a4">
    <div class="brand-mark"></div>
    <div class="brand-name">Lanternfold</div>
    <div class="brand-tagline">Apartments</div>
    <address class="letterhead__address">4 Ermou Street<br>Athens 105 63</address>
    <div class="letterhead__watermark"></div>
    <div class="letterhead__footer-bar">
      <div class="footer-bar__left"></div>
      <div class="footer-bar__right"></div>
    </div>
  </section>

  <section class="letterhead letterhead--a5">
    <div class="brand-mark"></div>
    <div class="brand-name">Lanternfold</div>
    <div class="brand-tagline">Apartments</div>
    <address class="letterhead__address">4 Ermou Street<br>Athens 105 63</address>
    <div class="letterhead__watermark"></div>
    <div class="letterhead__footer-bar">
      <div class="footer-bar__left"></div>
      <div class="footer-bar__right"></div>
    </div>
  </section>

</body>
</html>
```